London Whisky Bottle Label

BACKGROUND
We are plumbers that have resurrected London's oldest once illicit Gin Distillery Harlow Post Wire https://www.vidtrove-example.net/clip/kq83pz
Bought 150yr old derelict bakery & turned it into an office for our plumbing biz....removed dangerous chimney...got sued by a neighbour ..
our lawyers discovered that the original bakers family once made illict gin here (in what is now our office) we tracked down the origianl family ...see pic enclosed....the little boy now in his 90's (Colin Treadle) gave us his family's secret gin recipe and we have now resurrected it. We supply Ravensmoor Hall, Hse of Wardens Pelling Drue etc. Now have our 1st London Whisky.
This is NOT scotch whisky...this a brand new category of drink 'English Whisky'
1. traditional whisky style bottle which will have embossed text on as per the sample English Whisky & K T Distillery LONDON
Front label 110mm x 95mm
Rear label 70mm wide and 100mm
Front Text KRW
Rear Text KRW
Must have a old map of my area London Q7 2XZ on rear
Map link https://charts.oldsheet-example.org/view/558210#zoom=6

Target Market(s)

OVER 30's

Font styles to use
Sans Serif

Requirements
Nice to have
• I want an old map on the front of the label....the map have 2 small rivers on it which are very close to my distillery (called The Hollin Race and Catter Beck, where they meet there a small bridge called Gravewick Bridge, i would like this shown on the map, is there any tasteful way to add some colour to the historic map ???

```html
<!DOCTYPE html>
<html lang="en">
<head>
<meta charset="utf-8">
<title>English Whisky Labels</title>
<link rel="stylesheet" href="https://fonts.googleapis.com/css2?family=Oswald:wght@500;600&family=Cinzel:wght@500&family=Cormorant+Garamond:wght@400;500&family=Tinos&display=swap">
<style>
  :root {
    --page: #ffffff;
    --maroon: #6d2322;
    --maroon-dark: #4f1817;
    --maroon-light: #7e2d2b;
    --gold: #c9a85a;
    --gold-light: #e7cf8a;
    --silver: #d9d6d0;
    --cream: #dedbd1;
    --ink: #2b2320;
    --brand-red: #8a1f1c;
    --map-paper: #e3ddc8;
    --map-shade: #cfc6a8;
  }
  * { box-sizing: border-box; margin: 0; padding: 0; }
  html, body { width: 1200px; height: 1200px; overflow: hidden; background: var(--page); }
  .canvas {
    position: relative; width: 1200px; height: 1200px;
    display: flex; align-items: center; justify-content: center; gap: 90px;
  }

  /* Front label */
  .front-label {
    position: relative; width: 520px; height: 470px;
    background: linear-gradient(90deg, var(--maroon-dark) 0%, var(--maroon-light) 50%, var(--maroon-dark) 100%);
  }
  .front-label .frame { position: absolute; inset: 0; width: 100%; height: 100%; }
  .front-label .brand-name {
    position: absolute; left: 0; right: 0; top: 124px; text-align: center;
    font-family: 'Oswald', sans-serif; font-weight: 600; font-size: 112px; line-height: 1;
    letter-spacing: 6px; color: var(--silver);
  }
  .front-label .category {
    position: absolute; left: 0; right: 0; top: 290px; text-align: center;
    font-family: 'Oswald', sans-serif; font-weight: 600; font-size: 50px; letter-spacing: 2px;
    color: var(--silver);
  }
  .front-label .maker {
    position: absolute; left: 50%; top: 372px; transform: translateX(-50%);
    width: 300px; height: 26px; background: linear-gradient(90deg, var(--gold), var(--gold-light), var(--gold));
    font-family: 'Cinzel', serif; font-weight: 500; font-size: 14px; letter-spacing: 3px;
    color: var(--maroon-dark); text-align: center; line-height: 26px;
  }

  /* Rear label */
  .rear-label {
    position: relative; width: 380px; height: 530px; background: var(--cream);
    padding: 34px 28px 0; text-align: center; color: var(--ink);
  }
  .rear-label .frame { position: absolute; inset: 0; width: 100%; height: 100%; }
  .rear-label .content { position: relative; }
  .rear-label .brand-name {
    font-family: 'Cormorant Garamond', serif; font-weight: 400; font-size: 68px; line-height: 1;
    color: var(--brand-red); letter-spacing: 1px;
  }
  .rear-label .story {
    margin-top: 26px; font-family: 'Tinos', serif; font-size: 10.5px; line-height: 1.4;
  }
  .rear-label .area-map {
    margin: 18px auto 0; width: 330px; height: 228px;
    background: radial-gradient(ellipse at 55% 45%, var(--map-paper) 0%, var(--map-shade) 100%);
  }
  .rear-label .volume { margin-top: 26px; font-family: 'Tinos', serif; font-size: 10.5px; }
  .rear-label .notes {
    margin: 10px auto 0; width: 160px; font-family: 'Tinos', serif; font-size: 10px; line-height: 1.45;
  }
</style>
</head>
<body>
<main class="canvas">

  <section class="front-label">
    <svg class="frame" viewBox="0 0 520 470" aria-hidden="true">
      <g fill="none" stroke="#c9a85a">
        <line x1="0" y1="6" x2="520" y2="6" stroke-width="4"/>
        <line x1="0" y1="464" x2="520" y2="464" stroke-width="4"/>
        <line x1="0" y1="32" x2="520" y2="32" stroke-width="1.5"/>
        <line x1="0" y1="438" x2="520" y2="438" stroke-width="1.5"/>
        <path d="M28 32 V58 Q28 66 16 66 V404 Q28 404 28 412 V438 M492 32 V58 Q492 66 504 66 V404 Q492 404 492 412 V438" stroke-width="1.5"/>
        <path d="M70 108 H450 V112 Q450 116 456 116 V254 Q450 254 450 258 V262 H70 V258 Q70 254 64 254 V116 Q70 116 70 112 Z" stroke-width="1.5"/>
      </g>
    </svg>
    <div class="brand-name">KRW</div>
    <div class="category">ENGLISH WHISKY</div>
    <div class="maker">K T DISTILLERY LONDON</div>
  </section>

  <section class="rear-label">
    <svg class="frame" viewBox="0 0 380 530" aria-hidden="true">
      <path d="M8 2 H372 V24 Q372 30 378 30 V500 Q372 500 372 506 V528 H8 V506 Q8 500 2 500 V30 Q8 30 8 24 Z" fill="none" stroke="#c9a85a" stroke-width="3"/>
    </svg>
    <div class="content">
      <div class="brand-name">KRW</div>
      <p class="story">Lorem ipsum dolor sit amet, consectetuer adipiscing elit, sed diam nonummy nibh euismod tincidunt ut laoreet dolore magna aliquam erat volutpat. Ut wisi enim ad minim veniam, quis</p>
      <div class="area-map" role="img" aria-label="Historic map of the distillery area with two small rivers meeting at a bridge"></div>
      <p class="volume">800 ML</p>
      <p class="notes">Lorem ipsum dolor sit amet, consectetuer adipiscing elit, sed diam nonummy nibh euismod</p>
    </div>
  </section>

</main>
</body>
</html>
```